Redesign current business card for food company

i would like to redesign my business card. our company is food company, our product range from chips, juices, milk and etc (mostly dried food stuff).
I want o keep same logo but , the rest is open to new design.
you can check at our website about our company www.orvelpantry.com

Target Market(s)

most of food company

Industry/Entity Type

Business

Contact Information for Business Card

I want to keep more to blue color...

Colors
3176b5
abd036

Requirements
Must have
• our old logo
Nice to have
• we do not mind to have nice material on bus card in order to accomplish nice design. for example: using spot uv, embossed and etc.

```html
<!DOCTYPE html>
<html lang="en">
<head>
<meta charset="utf-8">
<title>Orvel Pantry — Business Card</title>
<link rel="stylesheet" href="https://fonts.googleapis.com/css2?family=Open+Sans:wght@400;600&display=swap">
<style>
  :root {
    --backdrop: #e9e7e4;
    --card-dark: #141516;
    --card-dark-edge: #202224;
    --brand-blue: #3176b5;
    --brand-blue-light: #2f8fd6;
    --back-blue-top: #2a8ad0;
    --back-blue-bottom: #1d5fa3;
    --text-light: #e4e6e8;
    --rule: #3a3d40;
    --accent-warm: #f7b21c;
  }
  * { margin: 0; padding: 0; box-sizing: border-box; }
  html, body {
    width: 1200px; height: 844px; overflow: hidden;
    background: var(--backdrop);
    font-family: "Open Sans", Arial, sans-serif;
  }
  .stage {
    position: relative; width: 1200px; height: 844px;
    display: flex; align-items: center; justify-content: center; gap: 60px;
  }
  .card {
    width: 500px; height: 286px; border-radius: 3px;
    position: relative; overflow: hidden;
    box-shadow: 0 10px 24px rgba(0,0,0,.18);
  }
  .card-front {
    background: linear-gradient(160deg, var(--card-dark-edge), var(--card-dark));
  }
  .wordmark {
    position: absolute; left: 40px; top: 108px;
    font-weight: 600; font-size: 76px; line-height: 1;
    color: var(--brand-blue-light); letter-spacing: -1px;
  }
  .divider {
    position: absolute; left: 268px; top: 38px; bottom: 38px;
    width: 1px; background: var(--rule);
  }
  .contact {
    position: absolute; left: 284px; top: 36px; right: 20px;
    color: var(--text-light);
  }
  .contact-name {
    font-weight: 600; font-size: 15px; color: var(--brand-blue-light);
  }
  .contact-title { font-size: 12px; margin-bottom: 10px; }
  .contact-list { list-style: none; font-size: 12px; line-height: 19px; }
  .contact-list li { display: flex; align-items: center; gap: 8px; }
  .contact-list svg { width: 10px; height: 10px; fill: var(--brand-blue-light); flex: none; }
  .contact-address { font-size: 12px; margin-top: 18px; }
  .card-back {
    background: linear-gradient(160deg, var(--back-blue-top), var(--back-blue-bottom));
    display: flex; align-items: center; justify-content: center; gap: 16px;
  }
  .back-mark {
    width: 26px; height: 26px; border-radius: 50%;
    background: var(--accent-warm);
  }
  .back-wordmark {
    font-weight: 600; font-size: 58px; color: var(--text-light); letter-spacing: -1px;
  }
</style>
</head>
<body>
<main class="stage">
  <section class="card card-front">
    <div class="wordmark">orvel</div>
    <div class="divider"></div>
    <div class="contact">
      <div class="contact-name">Daniel Hartono</div>
      <div class="contact-title">President</div>
      <ul class="contact-list">
        <li><svg viewBox="0 0 10 10"><path d="M2 1h2l1 2-1.2 1a5 5 0 0 0 2.2 2.2L7 5l2 1v2c0 .6-.4 1-1 1A8 8 0 0 1 1 2c0-.6.4-1 1-1z"/></svg>555 014 2230</li>
        <li><svg viewBox="0 0 10 10"><rect x="2" y="1" width="6" height="3"/><rect x="0.5" y="4" width="9" height="5" rx="1"/></svg>555 014 2231</li>
        <li><svg viewBox="0 0 10 10"><rect x="2.5" y="0.5" width="5" height="9" rx="1"/></svg>555 019 7742</li>
        <li><svg viewBox="0 0 10 10"><path d="M0.5 2h9v6h-9z M0.5 2l4.5 3.5L9.5 2" /></svg>daniel@orvelpantry.com</li>
        <li><svg viewBox="0 0 10 10"><circle cx="5" cy="5" r="4.5"/></svg>www.orvelpantry.com</li>
      </ul>
      <div class="contact-address">418 W Linden Ave.Ashford CA 90210</div>
    </div>
  </section>
  <section class="card card-back">
    <span class="back-mark"></span>
    <span class="back-wordmark">orvel</span>
  </section>
</main>
</body>
</html>
```